Velvet Moon Wheel Method Needs a Website

I require a Wordpress website so that I can do simple edits myself. I want it to be a fairly simple design as the videos and the text will speak for themselves.
The concept is simple, we have developed a revolutionary roulette system that proves the game is NOT random. This breakthrough is absolutely massive. We are offering a 12-part training course to take a beginner to a professional at their own pace through watching videos made by our roulette genius.
Roulette and casinos have a glitzy feel about them and this should be reflected in the style of the site. The roulette wheel, table and chips are very evocative and pictures of these would be good.
There is a home page and 5 other pages containing sub-pages. These should be interlinked and it must be easy to get back to the home page from anywhere on the site.
Coinvey links should appear at the bottom of each page.
I really need the site in a hurry as we were let down badly by the last developer we hired who went on holiday and left us in the lurch.

Target Market(s)

Gamblers, betting community, opportunity seekers

Coding

Coded - Design and coding required

Number of Pages Required

1 page

Font styles to use
Sans Serif

Requirements
Must have
• At least two videos on the Home page.
• Coinvey details on every page and tab.
• A box for name and email address for interested parties to leave their details.

```html
<!DOCTYPE html>
<html lang="en">
<head>
<meta charset="utf-8">
<title>Velvet Moon Wheel Method</title>
<link href="https://fonts.googleapis.com/css2?family=Open+Sans:wght@400;600;700&family=Oxygen:wght@400;700&display=swap" rel="stylesheet">
<style>
:root{
  --red:#e8302c;
  --side:#171717;
  --nav:#242424;
  --nav-line:#2f2f2f;
  --nav-active:#0f0f0f;
  --foot:#0c0c0c;
  --foot-text:#c9c9c9;
  --body:#555;
  --white:#fff;
}
*{margin:0;padding:0;box-sizing:border-box}
html,body{width:800px;height:1200px;overflow:hidden;background:var(--white)}
body{position:relative;font-family:"Open Sans",sans-serif;color:var(--body)}
.sidebar{position:absolute;left:0;top:0;width:171px;height:954px;background:var(--side)}
.brand{position:absolute;left:0;top:36px;width:171px;text-align:center;font-family:"Oxygen",sans-serif;color:var(--red);font-size:19px;line-height:24px}
.nav{position:absolute;top:128px;left:0;width:171px;list-style:none}
.nav li{position:relative;height:28.6px;background:var(--nav);border-bottom:1px solid var(--nav-line);font-family:"Oxygen",sans-serif;font-size:8px;color:var(--white);line-height:28px;padding-left:10px;text-transform:uppercase}
.nav li.active{background:var(--nav-active);color:var(--red)}
.nav li.sub{background:var(--side);text-transform:none;font-family:"Open Sans",sans-serif;font-size:7px;padding-left:22px}
.nav li.sub span{display:inline-block;width:20px}
.nav svg{position:absolute;right:12px;top:10px}
.hero{position:absolute;left:186px;top:19px;width:596px;height:200px;background:radial-gradient(ellipse at 15% 70%,#5a1a18 0%,#2a0d0c 30%,#0a0a0a 60%)}
.hero h1{position:absolute;left:0;width:100%;top:66px;text-align:center;font-family:"Oxygen",sans-serif;font-weight:700;color:var(--red);font-size:26px;line-height:33px}
.dots{position:absolute;top:189px;left:284px;display:flex;gap:4px}
.dots i{width:3.5px;height:3.5px;border-radius:50%;background:#bbb}
.dots i:first-child{background:var(--red)}
.copy{position:absolute;left:186px;width:596px;font-size:8px;line-height:11.4px;letter-spacing:-0.12px;hyphens:auto}
.copy p+p{margin-top:11.4px}
.copy strong{font-size:10.3px;color:#222;font-weight:600;letter-spacing:0}
.video{position:absolute;left:186px;top:369px;width:596px;height:132px;background:linear-gradient(90deg,#3a2a20 0%,#6b2a1c 35%,#8a4a24 65%,#5a3018 100%)}
.play{position:absolute}
.link-red{position:absolute;left:186px;top:581px;font-size:8px;color:var(--red)}
.twocol{width:344px}
.wheel-video{position:absolute;left:548px;top:592px;width:244px;height:232px;background:radial-gradient(ellipse 44% 42% at 50% 50%,#a03a22 0%,#7a3418 45%,#3a2416 80%,#fff 100%)}
.footer{position:absolute;left:0;top:954px;width:800px;height:246px;background:var(--foot);color:var(--foot-text);font-size:8px}
.footer h4{position:absolute;top:32px;font-size:8px;font-weight:400;color:var(--red);letter-spacing:.3px}
.about{position:absolute;left:66px;top:58px;width:180px;line-height:12px}
.readmore{position:absolute;left:66px;top:132px;color:var(--red)}
.social{position:absolute;left:66px;top:156px;display:flex;gap:11px}
.social i{width:12px;height:12px;border-radius:50%;background:#8a8a8a}
.links{position:absolute;left:270px;top:58px;list-style:none;line-height:20.4px}
.contact{position:absolute;left:400px;top:58px;width:152px}
.contact div{position:relative;padding-left:17px;height:30px;border-bottom:1px solid #222;font-size:7.6px;line-height:12px}
.contact svg{position:absolute;left:0;top:1px}
.field{position:absolute;left:582px;width:152px;height:18px;background:#262626;color:var(--white);font-size:6.4px;line-height:18px;padding-left:6px}
.send{position:absolute;left:650px;top:109px;width:84px;height:19px;background:var(--red);color:var(--white);font-size:6.4px;text-align:center;line-height:19px}
.rule{position:absolute;left:66px;right:66px;top:203px;height:1px;background:#1f1f1f}
.pay{position:absolute;left:66px;top:219px;display:flex;align-items:center;gap:4px;color:var(--white);font-size:7.5px}
.pay i{width:8px;height:8px;background:var(--foot-text)}
.copyright{position:absolute;right:66px;top:220px;color:var(--white);font-size:7.2px}
.copyright span{color:var(--red)}
</style>
</head>
<body>
<aside class="sidebar">
  <div class="brand">Velvet Moon<br>Wheel Method</div>
  <ul class="nav">
    <li>Home<svg width="6" height="6" viewBox="0 0 6 6"><path d="M0 2l3 2 3-2" stroke="#555" fill="none"/></svg></li>
    <li>Introduction<svg width="6" height="6" viewBox="0 0 6 6"><path d="M0 2l3 2 3-2" stroke="#555" fill="none"/></svg></li>
    <li>Training<svg width="6" height="6" viewBox="0 0 6 6"><path d="M0 2l3 2 3-2" stroke="#555" fill="none"/></svg></li>
    <li class="active">Casinos<svg width="6" height="6" viewBox="0 0 6 6"><path d="M0 4l3-2 3 2" stroke="#e8302c" fill="none"/></svg></li>
    <li class="sub"><span>1.</span>Reputable Casinos<svg width="6" height="6" viewBox="0 0 6 6"><path d="M3 0v6M0 3h6" stroke="#777"/></svg></li>
    <li class="sub"><span>2.</span>Casino Bonuses<svg width="6" height="6" viewBox="0 0 6 6"><path d="M3 0v6M0 3h6" stroke="#777"/></svg></li>
    <li class="sub"><span>3.</span>RNG vs Real Wheel<svg width="6" height="6" viewBox="0 0 6 6"><path d="M3 0v6M0 3h6" stroke="#777"/></svg></li>
    <li class="sub"><svg width="6" height="6" viewBox="0 0 6 6"><path d="M3 0v6M0 3h6" stroke="#777"/></svg></li>
    <li>Coaching<svg width="6" height="6" viewBox="0 0 6 6"><path d="M3 0v6M0 3h6" stroke="#777"/></svg></li>
    <li>Overseas Trip<svg width="6" height="6" viewBox="0 0 6 6"><path d="M0 2l3 2 3-2" stroke="#555" fill="none"/></svg></li>
    <li>FAQ<svg width="6" height="6" viewBox="0 0 6 6"><path d="M0 2l3 2 3-2" stroke="#555" fill="none"/></svg></li>
  </ul>
</aside>

<section class="hero" role="img" aria-label="Close-up photo of a roulette wheel with the ball resting on the numbers">
  <h1>Velvet Moon<br>at Roulette</h1>
  <div class="dots"><i></i><i></i><i></i><i></i></div>
</section>

<div class="copy" style="top:252px">
  <p><strong>Introducing the incredible Velvet Moon roulette system.</strong> Four years in the making by a roulette genius who has observed hundreds of thousands of spins to create a truly groundbreaking system. Every aspect of the game has been broken down, analysed and rebuilt with a solution. This system questions whether the game of roulette is truly random......and the answer is a resounding NO !!</p>
  <p>The key to success is long term profits but to achieve that you need to look beyond complexity and concentrate on simplicity. The system reverses general logic and considers the number of losses rather than the number of wins. This led to the discovery of the counting system, a perfect, carefully balanced approach to progression that protects your bankroll at all times. This alone would be the perfect complement for any roulette system but when combined with the rules of Velvet Moon, it's dynamite.</p>
</div>

<div class="video" role="img" aria-label="Video: blurred still of a spinning roulette wheel">
  <svg class="play" style="left:279px;top:53px" width="26" height="26" viewBox="0 0 26 26"><circle cx="13" cy="13" r="13" fill="#e8302c"/><path d="M10 7l9 6-9 6z" fill="#fff"/></svg>
</div>

<div class="copy" style="top:524px">
  <p>The second major breakthrough was the discovery of the families. These are groups of numbers that appear regularly within a few spins of each other. For students learning the system, this is their first 'wow' moment. The regularity of hits between numbers in the families is staggering and underpins the whole system. Finally, the families were analysed further and broken down into pairs. This provided the opportunity to shorten the average playing time of each session to around half an hour. The philosophy of Velvet Moon is to build your stakes slowly and then when everything falls into place, make a big win and walk away.</p>
</div>

<div class="link-red">Watch this video and prepare to be amazed</div>

<div class="copy twocol" style="top:610px">
  <p>We are offering a unique opportunity to learn the Velvet Moon system through a series of videos made by our very own roulette genius. You will learn every aspect of this amazing system at your own pace, only moving on to the next stage when you have totally mastered the previous step. We encourage our students to practise their skills in play mode and when they are completely confident and winning every session, play with real money. This allows them to build their bankroll and pay for each video as they go along.</p>
  <p>Our course has been designed to make each step easy to learn and understand. Each video leads into the next and builds a new layer of understanding on top of the last. Committing the information to memory is very easy using this method and our students become experts at analysing everything unfolding before them in a roulette session.</p>
  <p>Some of our students become professional players, enjoying the thrills of playing in bricks and mortar casinos around the world. Others are happy to play part-time from home and build a second income. The fact is that once you have the skills to be successful at roulette, the options really are endless.</p>
  <p>We are only successful if our students achieve their goals. We provide individual coaching sessions if anyone needs extra tuition and will always endeavor to answer</p>
</div>

<div class="wheel-video" role="img" aria-label="Video: a wooden roulette wheel seen at an angle">
  <svg class="play" style="left:109px;top:103px" width="26" height="26" viewBox="0 0 26 26"><circle cx="13" cy="13" r="13" fill="#e8302c"/><path d="M10 7l9 6-9 6z" fill="#fff"/></svg>
</div>

<div class="copy" style="top:850px">
  <p>questions quickly. Upon completion of the course, we will also play for our students so that they can watch and learn.<br>The highlight of the year is undoubtedly the Velvet Moon Las Vegas trip. A chance to meet the team and fellow students who have learnt the system. The emphasis is very much on the 'business' of making money with a little 'pleasure' thrown in after a day of play at the tables.<br>We invite you to have a look around the site and ask us any questions. It will be our pleasure to enroll you as the next student of Velvet Moon.</p>
</div>

<footer class="footer">
  <h4 style="left:66px">ABOUT</h4>
  <h4 style="left:270px">LINKS</h4>
  <h4 style="left:400px">CONTACT INFO</h4>
  <h4 style="left:582px">NEWSLETTER SUBSCRIBE</h4>

  <p class="about">Lorem ipsum dolor sit amet, consectetur adipiscing elit. Nulla sodales, odio id dapibus pulvinar, augue risus efficitur ipsum, at venenatis dolor dui et leo. Praesent vulputate quis erat quis finibus.</p>
  <div class="readmore">Read More &gt;&gt;</div>
  <div class="social"><i></i><i></i><i></i><i></i><i></i><i></i></div>

  <ul class="links">
    <li>Privacy Policy</li>
    <li>Terms and Conditions</li>
    <li>Site Map</li>
    <li>Affiliates &amp; Vendors</li>
    <li>Contact Us</li>
  </ul>

  <div class="contact">
    <div><svg width="9" height="8" viewBox="0 0 9 8"><rect x=".5" y=".5" width="8" height="7" fill="none" stroke="#ccc"/><path d="M.5 .5l4 3.5 4-3.5" fill="none" stroke="#ccc"/></svg>hello@velvetmoonwheel.com</div>
    <div style="height:36px;padding-top:4px"><svg width="8" height="8" viewBox="0 0 8 8" style="top:5px"><path d="M1 0h2l1 2-1 1q1 2 2 2l1-1 2 1v2q-1 1-2 1Q0 8 0 1q0-1 1-1z" fill="#ccc"/></svg>07700 900417</div>
    <div style="height:46px;padding-top:8px"><svg width="8" height="8" viewBox="0 0 8 8" style="top:9px"><circle cx="4" cy="4" r="4" fill="#ccc"/></svg>Alden Marsh</div>
    <div style="border:0;padding-top:12px"><svg width="9" height="9" viewBox="0 0 9 9" style="top:13px"><circle cx="4.5" cy="4.5" r="4" fill="none" stroke="#ccc"/><path d="M.5 4.5h8M4.5 .5c-2 2-2 6 0 8M4.5 .5c2 2 2 6 0 8" fill="none" stroke="#ccc"/></svg>www.velvetmoonwheel.com</div>
  </div>

  <div class="field" style="top:60px">Name</div>
  <div class="field" style="top:82px">Email Address</div>
  <div class="send">SEND</div>

  <div class="rule"></div>
  <div class="pay"><i></i>Coinvey</div>
  <div class="copyright">Copyright © 2016 - <span>yoursite.</span> All Rights Reserved</div>
</footer>
</body>
</html>
```